I have a logo and need to design the business card and stationery.
Updates

The uploaded logo image named as GREYMARSH CONSTRUCTION which is to be replaced to GREYMARSH CONTRACTS. Kindly add below details and submit the designs- Company name- Greymarsh Engineering Contracts LLP Name & Post- Kelvan Joshi (Designated Partner) Address- Block No.317, Wing C, Tulvo Trade Court, Manek Pural Road, Ruparel Industrial Estate, Goregaon(E), Mumbai - 400 063 Contact- +91 97415 60382 Email- kelvanjoshi@mailbrook.example Website- www.greymarshcontracts.example Contact for Letterhead- +91-22-28754193

Hi Tovin Rahul, We are liking your Design #28860835. We have suggested some changes which are mentioned in feedback. Kindly revert with it asap to finalize this design.

Colors

Designer to choose colors to be used in the design.

```html
<!DOCTYPE html>
<html lang="en">
<head>
<meta charset="utf-8">
<title>Greymarsh Contracts — Letterhead</title>
<link href="https://fonts.googleapis.com/css2?family=Open+Sans:wght@400;700&family=Michroma&display=swap" rel="stylesheet">
<style>
  :root {
    --backdrop: #e4e4e6;
    --paper: #f7f7f9;
    --band: #333333;
    --band-text: #f2f2f2;
    --ink: #3a3a3a;
    --signature-tone: #d9d9dd;
  }
  * { margin: 0; padding: 0; box-sizing: border-box; }
  html, body {
    width: 676px; height: 1200px; overflow: hidden;
    background: var(--backdrop);
    font-family: "Open Sans", Arial, sans-serif;
  }
  .letterhead {
    position: absolute; left: 38px; top: 182px;
    width: 600px; height: 835px;
    background: var(--paper);
    box-shadow: 0 4px 14px rgba(0,0,0,.12);
  }
  .letterhead__header {
    position: absolute; left: 0; top: 0; width: 100%; height: 127px;
    background: var(--band); color: var(--band-text);
  }
  .brand {
    position: absolute; left: 52px; top: 30px;
    display: flex; align-items: center; gap: 10px;
  }
  .brand__square {
    width: 40px; height: 40px; border: 4px solid var(--band-text);
  }
  .brand__name {
    font-weight: 700; font-size: 15px; line-height: 19px; letter-spacing: 1px;
    color: var(--band-text);
  }
  .contact {
    position: absolute; left: 372px; top: 20px;
    font-size: 8.6px; line-height: 11px; color: var(--band-text);
  }
  .contact__lines { margin-top: 6px; }
  .contact__line { display: flex; align-items: center; gap: 4px; }
  .contact__line svg { width: 7px; height: 7px; fill: var(--band-text); }
  .letter {
    position: absolute; left: 54px; top: 214px; width: 500px;
    font-size: 10.3px; line-height: 16px; color: var(--ink);
  }
  .letter__greeting { margin-bottom: 16px; }
  .letter__paragraph { margin-bottom: 16px; }
  .letter__closing { margin-top: 4px; }
  .signature {
    position: absolute; left: 54px; top: 637px; width: 64px; height: 64px;
    background: var(--signature-tone);
  }
  .letterhead__footer {
    position: absolute; left: 0; bottom: 0; width: 100%; height: 20px;
    background: var(--band);
    display: flex; align-items: center; justify-content: center;
  }
  .tagline {
    font-family: "Michroma", "Open Sans", sans-serif;
    font-size: 6.5px; letter-spacing: 3.4px; color: var(--band-text);
  }
</style>
</head>
<body>
  <div class="letterhead">
    <header class="letterhead__header">
      <div class="brand">
        <div class="brand__square"></div>
        <div class="brand__name">GREYMARSH<br>CONTRACTS</div>
      </div>
      <div class="contact">
        <div>Greymarsh Engineering Contracts LLP<br>
        Block No.317, Wing C, Tulvo Trade Court,<br>
        Manek Pural Road, Ruparel Industrial Estate,<br>
        Goregaon(E), Mumbai - 400 063</div>
        <div class="contact__lines">
          <div class="contact__line"><svg viewBox="0 0 10 10"><path d="M2 0h2l1 3-1.5 1a6 6 0 0 0 2.5 2.5L7 5l3 1v2c0 1-1 2-2 2C4 10 0 6 0 2c0-1 1-2 2-2z"/></svg>+91-22-28754193</div>
          <div class="contact__line"><svg viewBox="0 0 10 10"><path d="M0 2h10v6H0z M0 2l5 3 5-3" stroke="#333" stroke-width=".8"/></svg>info@greymarshcontracts.example</div>
          <div class="contact__line"><svg viewBox="0 0 10 10"><circle cx="5" cy="5" r="5"/><path d="M0 5h10M5 0c-3 3-3 7 0 10M5 0c3 3 3 7 0 10" stroke="#333" stroke-width=".7" fill="none"/></svg>www.greymarshcontracts.example</div>
        </div>
      </div>
    </header>

    <main class="letter">
      <p class="letter__greeting">Dear customer,</p>
      <p class="letter__paragraph">Lorem ipsum dolor sit amet, consectetur adipisicing elit, sed do eiusmod tempor incididunt ut<br>labore et dolore magna aliqua. Ut enim ad minim veniam, quis nostrud exercitation ullamco<br>laboris nisi ut aliquip ex ea commodo consequat. Duis aute irure dolor in reprehenderit in<br>voluptate velit esse cillum dolore eu fugiat nulla pariatur. Excepteur sint occaecat cupidatat<br>non proident, sunt in culpa qui officia deserunt mollit anim id est laborum.</p>
      <p class="letter__paragraph">Lorem ipsum dolor sit amet, consectetur adipisicing elit, sed do eiusmod tempor incididunt ut<br>labore et dolore magna aliqua. Ut enim ad minim veniam, quis nostrud exercitation ullamco<br>laboris nisi ut aliquip ex ea commodo consequat. Duis aute irure dolor in reprehenderit in<br>voluptate velit esse cillum dolore eu fugiat nulla pariatur. Excepteur sint occaecat cupidatat<br>non proident, sunt in culpa qui officia deserunt mollit anim id est laborum.</p>
      <p class="letter__paragraph">Lorem ipsum dolor sit amet, consectetur adipisicing elit, sed do eiusmod tempor incididunt ut<br>labore et dolore magna aliqua. Ut enim ad minim veniam, quis nostrud exercitation ullamco<br>laboris nisi ut aliquip ex ea commodo consequat. Duis aute irure dolor in reprehenderit in<br>voluptate velit esse cillum dolore eu fugiat nulla pariatur. Excepteur sint occaecat cupidatat<br>non proident, sunt in culpa qui officia deserunt mollit anim id est laborum.</p>
      <p class="letter__paragraph">Lorem ipsum dolor sit amet, consectetur adipisicing elit, sed do eiusmod tempor incididunt ut<br>labore et dolore magna aliqua. Ut enim ad minim veniam, quis nostrud exercitation ullamco<br>laboris nisi ut aliquip ex ea commodo consequat. Duis aute irure dolor in reprehenderit.</p>
      <p class="letter__closing">Yours Sincerely,</p>
    </main>

    <div class="signature" role="img" aria-label="Handwritten signature"></div>

    <footer class="letterhead__footer">
      <span class="tagline">BUILT ON SOLID GROUND.</span>
    </footer>
  </div>
</body>
</html>
```